Report template for evaluation reports to be used by non designers

We are looking for a report template that meets all the requirements listed in the attached documents. letter head, logo etc have been enclosed. Its important that the colour integrity is kept, but beyond that options are welcome.
Its important that the document is extremely easy to use and that is able to be adapted to include eatables, figures, pictures, text boxes etc and keep the integrity of the template

Target Market(s)

Governments, Civil society organisations and research institutions

Font styles to use
Sans Serif

Colors
6b449b
876aae
c0c0c0
000000

Requirements
Must have
• Clean, professional, not concluded, modern, must be easy to use
Should not have
• too busy, hard to use

```html
<!DOCTYPE html>
<html lang="en">
<head>
<meta charset="utf-8">
<title>Civic Insight Institute – Report 2018 Cover</title>
<link href="https://fonts.googleapis.com/css2?family=Oswald:wght@700&family=Open+Sans:wght@400;600;700&display=swap" rel="stylesheet">
<style>
  :root{
    --purple:#6b449b;
    --lilac:#876aae;
    --silver:#c0c0c0;
    --black:#000000;
    --ink:#2b2b2b;
    --grey-text:#8a8a8a;
    --faint:#ededed;
    --backdrop:#d6d6d6;
    --paper:#ffffff;
  }
  *{margin:0;padding:0;box-sizing:border-box}
  html,body{width:1200px;height:847px;overflow:hidden}
  body{background:var(--backdrop);font-family:"Open Sans",Arial,sans-serif;position:relative}
  .page{position:absolute;top:42px;width:540px;height:764px;background:var(--paper);overflow:hidden;box-shadow:0 4px 14px rgba(0,0,0,.18)}
  .page--back{left:60px}
  .page--front{left:600px}
  .page svg.art{position:absolute;inset:0}

  /* back cover */
  .top-rule{position:absolute;left:0;top:0;width:100%;height:6px;background:var(--purple)}
  .world-map{position:absolute;left:10px;top:40px;width:500px;height:420px;
    background:radial-gradient(ellipse at 45% 45%,#e6e6e6 0%,#efefef 55%,rgba(255,255,255,0) 80%);border-radius:30px}
  .org-name{font-family:"Open Sans",Arial,sans-serif;font-weight:600;color:var(--ink);letter-spacing:.18em;text-transform:uppercase;text-align:center;display:flex;align-items:center;justify-content:center;gap:12px}
  .org-name .dot{width:14px;height:14px;border-radius:50%;background:var(--purple);flex:none}
  .page--back .org-name{position:absolute;left:0;right:0;top:540px;font-size:17px}
  .contacts{position:absolute;left:30px;right:30px;top:615px;display:flex;justify-content:space-between}
  .contact{width:150px;text-align:center;font-size:9.5px;line-height:1.45;color:var(--grey-text)}
  .contact .icon{width:48px;height:48px;border-radius:50%;margin:0 auto 10px;display:flex;align-items:center;justify-content:center}
  .contact .icon--light{background:var(--lilac)}
  .contact .icon--dark{background:var(--purple)}

  /* front cover */
  .cover-title{position:absolute;right:26px;top:250px;text-align:right}
  .cover-title .word{font-family:"Oswald",Impact,sans-serif;font-weight:700;font-size:58px;line-height:1;color:var(--purple);letter-spacing:.01em}
  .cover-title .year{font-family:"Open Sans",Arial,sans-serif;font-weight:700;font-size:42px;line-height:1.1;color:var(--silver);letter-spacing:.42em;margin-right:-.42em}
  .page--front .org-name{position:absolute;left:0;right:0;top:630px;font-size:19px}
  .registration{position:absolute;left:0;right:0;top:668px;text-align:center;font-size:8px;font-weight:700;color:var(--purple)}
</style>
</head>
<body>

<section class="page page--back" aria-label="Back cover">
  <div class="top-rule"></div>
  <div class="world-map" role="img" aria-label="Faint grey world map"></div>

  <p class="org-name"><span class="dot"></span>Civic Insight Institute</p>

  <div class="contacts">
    <div class="contact">
      <div class="icon icon--light">
        <svg width="22" height="22" viewBox="0 0 24 24" aria-hidden="true"><circle cx="12" cy="8" r="4.2" fill="#fff"/><path d="M3.5 21c0-4.6 3.8-7.5 8.5-7.5s8.5 2.9 8.5 7.5z" fill="#fff"/></svg>
      </div>
      +41 70 000 00 00
    </div>
    <div class="contact">
      <div class="icon icon--dark">
        <svg width="22" height="22" viewBox="0 0 24 24" aria-hidden="true"><circle cx="14" cy="9.5" r="5.5" fill="none" stroke="#fff" stroke-width="2.4"/><path d="M10 13.5 4 19.5" stroke="#fff" stroke-width="2.8" stroke-linecap="round"/></svg>
      </div>
      info@civicinsight.org<br>www.civicinsight.org
    </div>
    <div class="contact">
      <div class="icon icon--dark">
        <svg width="22" height="22" viewBox="0 0 24 24" aria-hidden="true"><path d="M12 3 2 12h3v8h5v-5h4v5h5v-8h3z" fill="#fff"/></svg>
      </div>
      00 Sample Lane,<br>Harbour View, NZ00000
    </div>
  </div>
</section>

<section class="page page--front" aria-label="Front cover">
  <svg class="art" width="540" height="764" viewBox="0 0 540 764">
    <defs>
      <linearGradient id="photoTone" x1="0" y1="0" x2="1" y2="1">
        <stop offset="0" stop-color="#4a4a4a"/>
        <stop offset=".5" stop-color="#9a9a9a"/>
        <stop offset="1" stop-color="#6e6e6e"/>
      </linearGradient>
    </defs>
    <polygon points="0,0 540,0 540,150 330,225 220,185 0,300" fill="url(#photoTone)" role="img" aria-label="Blurred city skyline photograph"/>
    <polygon points="0,300 220,185 330,225 150,290 0,380" fill="#b9b9b9"/>
    <polygon points="220,185 330,225 300,236 230,200" fill="#8e8e8e"/>
    <polygon points="330,225 540,80 540,215" fill="#6b449b"/>
    <polygon points="370,764 540,764 540,590" fill="#6b449b"/>
  </svg>

  <div class="cover-title">
    <div class="word">REPORT</div>
    <div class="year">2018</div>
  </div>

  <p class="org-name"><span class="dot"></span>Civic Insight Institute</p>
  <p class="registration">Registration Number: CHF-000.000.000</p>
</section>

</body>
</html>
```